Upland Bird Hunting Preserve and Pointing Dog kennel

Need Price packages outlined for the bird hunting business. List the kennel and that we provide training and dogs for sale.
The preserve is "Tall Heron Provisions" the dog kennel is "Pine Hollow Setters"
1/2 Day Upland Field Hunts: 5 Pheasants $120
7 Chukar $125
Continental Hunt 12 Pheasants $325 includes meal, minimum 12 hunters
Guides available $100

Target Market(s)

upland bird hunters

Industry/Entity Type

hunting, outdoor

Colors
EE7325
F08F49
F5BC92
FAE3D3
FDF4ED

```html
<!DOCTYPE html>
<html lang="en">
<head>
<meta charset="utf-8">
<title>Tall Heron Provisions – Upland Bird Preserve Flyer</title>
<link rel="stylesheet" href="https://fonts.googleapis.com/css2?family=Anton&family=Oswald:wght@400;500;600;700&display=swap">
<style>
:root{
  --stage:#9c9c9c;
  --paper:#e4ebcf;
  --paper-deep:#d3ddb4;
  --olive:#4c6125;
  --forest:#2f4a1a;
  --gold:#c7a222;
  --ink:#1d1d1b;
  --white:#ffffff;
}
*{box-sizing:border-box;margin:0;padding:0}
html,body{width:981px;height:1200px;overflow:hidden}
body{background:var(--stage);font-family:"Oswald",sans-serif;color:var(--ink);position:relative}
.flyer{position:absolute;left:92px;top:92px;width:797px;height:1031px;background:linear-gradient(180deg,var(--paper) 0%,#e8eed6 60%,var(--paper-deep) 100%);overflow:hidden}
.photo{position:absolute;display:block}
.photo-group{left:0;top:0;width:797px;height:300px}
.photo-family{left:0;top:716px;width:520px;height:262px}
.photo-pointer{left:500px;top:790px;width:297px;height:188px}

.headline{position:absolute;left:46px;top:180px;font-family:"Anton",sans-serif;font-size:60px;line-height:64px;color:var(--gold);letter-spacing:-0.5px;
  text-shadow:2px 2px 0 var(--white),-2px -2px 0 var(--white),2px -2px 0 var(--white),-2px 2px 0 var(--white),0 3px 0 var(--white),3px 0 0 var(--white),-3px 0 0 var(--white),0 -3px 0 var(--white)}
.headline span{display:block}
.preserve-type{position:absolute;left:46px;top:388px;font-family:"Anton",sans-serif;font-size:46px;line-height:50px;color:var(--olive);
  text-shadow:2px 2px 0 var(--white),-2px -2px 0 var(--white),2px -2px 0 var(--white),-2px 2px 0 var(--white)}
.preserve-type span{display:block}
.preserve-type .dark{color:var(--forest)}

.continental{position:absolute;left:46px;top:508px;font-size:29px;font-weight:600;color:var(--ink);letter-spacing:-0.3px}
.continental em{font-style:normal;color:var(--olive)}
.perk{position:absolute;top:559px;height:48px;border:1.5px solid var(--olive);border-radius:14px;padding:4px 0 0 22px;font-size:16px;line-height:18px;color:var(--ink)}
.perk .tick{position:absolute;left:-10px;top:13px;width:20px;height:20px}
.perk-min{left:48px;width:102px}
.perk-price{left:164px;width:102px}
.perk-birds{left:279px;width:150px}
.note{position:absolute;left:44px;top:616px;font-size:16px;color:var(--ink);display:flex;align-items:center;gap:6px}

.contact{position:absolute;left:39px;top:659px;width:401px;height:52px;border-radius:12px;overflow:hidden;background:var(--ink);z-index:2}
.contact .name{position:absolute;left:0;top:0;height:100%;width:188px;background:var(--olive);clip-path:polygon(0 0,90% 0,100% 100%,0 100%);padding-left:17px;display:flex;align-items:center;font-size:30px;font-weight:600;letter-spacing:-0.5px;color:var(--white);white-space:nowrap}
.contact .icon{position:absolute;left:169px;top:7px;width:38px;height:38px}
.contact .phone{position:absolute;left:213px;top:0;height:100%;display:flex;align-items:center;font-size:30px;font-weight:600;color:var(--white);white-space:nowrap}

.packages{position:absolute;left:485px;top:290px}
.packages h2{font-size:35px;font-weight:600;color:var(--ink);line-height:42px}
.packages h3{font-size:37px;font-weight:600;color:var(--olive);line-height:44px}
.price-box{position:absolute;width:132px;height:80px;border:1.5px solid var(--olive);border-radius:12px;text-align:center}
.price-box .item{display:block;font-size:19px;font-weight:600;color:var(--ink);margin-top:8px;line-height:22px}
.price-box .amount{display:block;font-family:"Anton",sans-serif;font-size:38px;color:var(--gold);line-height:44px}
.box-pheasant{left:482px;top:390px}
.box-chukar{left:622px;top:390px}
.box-quail{left:482px;top:479px}
.guide{position:absolute;left:626px;top:484px}
.guide .label{font-size:20px;font-weight:600;color:var(--ink);line-height:24px}
.guide .amount{font-family:"Anton",sans-serif;font-size:38px;color:var(--olive);line-height:46px}
.guide .unit{display:inline-block;font-size:16px;font-weight:600;color:var(--olive);line-height:17px;vertical-align:6px;margin-left:4px}

.kennel-mark{position:absolute;left:485px;top:598px;width:310px;display:flex;align-items:center;justify-content:center;gap:8px;font-size:23px;font-weight:500;color:var(--ink);letter-spacing:1px;white-space:nowrap}
.kennel-mark i{display:block;width:14px;height:14px;border-radius:50%;background:var(--ink)}
.kennel-rule{position:absolute;left:522px;top:675px;width:193px;height:3px;background:var(--ink)}
.kennel-town{position:absolute;left:485px;top:684px;width:310px;text-align:center;font-size:19px;line-height:24px;font-weight:500;letter-spacing:1px;color:var(--ink)}
.kennel-offer{position:absolute;left:485px;top:718px;width:310px;text-align:center;font-size:29px;font-weight:600;line-height:31px;color:var(--ink)}
.kennel-offer em{font-style:normal;color:var(--olive)}

.footer{position:absolute;left:0;top:976px;width:797px;height:55px;background:var(--olive);display:flex;align-items:center;justify-content:center;gap:8px;font-size:23px;font-weight:600;color:var(--white)}
</style>
</head>
<body>
<main class="flyer">
  <svg class="photo photo-group" viewBox="0 0 797 300" role="img" aria-label="Photo of a group of hunters standing behind a log lined with harvested pheasants in winter woods">
    <defs>
      <linearGradient id="woods" x1="0" y1="0" x2="0" y2="1">
        <stop offset="0" stop-color="#b99a74"/>
        <stop offset="0.5" stop-color="#8a6f55"/>
        <stop offset="1" stop-color="#4a3a2c"/>
      </linearGradient>
    </defs>
    <polygon points="0,0 797,0 797,245 740,250 690,262 620,258 560,270 520,262 470,282 430,266 380,276 330,262 270,274 210,258 150,270 90,255 0,268" fill="url(#woods)"/>
  </svg>

  <h1 class="headline"><span>TALL HERON</span><span>PROVISIONS, LLC</span><span>ASHFORD, MO</span></h1>
  <p class="preserve-type"><span>LICENSED UPLAND</span><span class="dark">BIRD PRESERVE</span></p>

  <p class="continental">Continental <em>Pheasant Hunt</em></p>
  <div class="perk perk-min"><svg class="tick" viewBox="0 0 20 20"><circle cx="10" cy="10" r="10" fill="#c7a222"/><path d="M5.5 10.5l3 3 6-6.5" stroke="#fff" stroke-width="2" fill="none"/></svg>12 hunter<br>minimum</div>
  <div class="perk perk-price"><svg class="tick" viewBox="0 0 20 20"><circle cx="10" cy="10" r="10" fill="#c7a222"/><path d="M5.5 10.5l3 3 6-6.5" stroke="#fff" stroke-width="2" fill="none"/></svg>$325<br>per hunter</div>
  <div class="perk perk-birds"><svg class="tick" viewBox="0 0 20 20"><circle cx="10" cy="10" r="10" fill="#c7a222"/><path d="M5.5 10.5l3 3 6-6.5" stroke="#fff" stroke-width="2" fill="none"/></svg>Includes 12<br>pheasants and meal</div>
  <p class="note"><svg width="18" height="18" viewBox="0 0 18 18"><rect x="3.5" y="3.5" width="11" height="11" transform="rotate(45 9 9)" fill="none" stroke="#4c6125" stroke-width="1.5"/><path d="M6 9l2 2 4-4" stroke="#4c6125" stroke-width="1.5" fill="none"/></svg>All hunts include bird Cleaning and lodging available</p>

  <div class="contact">
    <span class="name">Dale Morgan</span>
    <svg class="icon" viewBox="0 0 38 38"><circle cx="19" cy="19" r="18" fill="#c7a222"/><circle cx="19" cy="19" r="13" fill="none" stroke="#fff" stroke-width="1.5"/><path d="M14 12c1-1 2-1 3 0l1.5 2.5c.5 1 0 1.8-.8 2.3-.6.4-.6 1 0 2l2 2.5c.7.8 1.3.8 2 .3.8-.7 1.6-.9 2.4-.3l2.2 1.7c1 .8.8 1.8 0 2.6-2 2-5 1.5-8-1.5s-5.5-6.5-5.3-9.3c0-1.2.4-2 1-2.8z" fill="#fff"/></svg>
    <span class="phone">660-555-0147</span>
  </div>

  <section class="packages">
    <h2>Hunting Packages</h2>
    <h3>1/2-day field hunts</h3>
  </section>
  <div class="price-box box-pheasant"><span class="item">5 Pheasants</span><span class="amount">$120</span></div>
  <div class="price-box box-chukar"><span class="item">7 Chukar</span><span class="amount">$125</span></div>
  <div class="price-box box-quail"><span class="item">10 Quail</span><span class="amount">$125</span></div>
  <div class="guide"><p class="label">Guide Available</p><p class="amount">$100<span class="unit">per<br>half day</span></p></div>

  <p class="kennel-mark"><i></i>PINE HOLLOW SETTERS</p>
  <div class="kennel-rule"></div>
  <p class="kennel-town">ELM SPRINGS, MO</p>
  <p class="kennel-offer">Training, puppies and<br>started dogs <em>available</em></p>

  <svg class="photo photo-family" viewBox="0 0 520 262" role="img" aria-label="Photo of hunters in blaze orange with a boy, a yellow retriever and a row of harvested birds">
    <defs>
      <linearGradient id="field" x1="0" y1="0" x2="0" y2="1">
        <stop offset="0" stop-color="#b5a184"/>
        <stop offset="0.45" stop-color="#d98a2a"/>
        <stop offset="1" stop-color="#5a6b2b"/>
      </linearGradient>
    </defs>
    <polygon points="0,24 120,20 190,10 250,2 300,18 380,32 440,38 470,90 500,170 520,262 0,262" fill="url(#field)"/>
  </svg>
  <svg class="photo photo-pointer" viewBox="0 0 297 188" role="img" aria-label="Photo of a ticked pointing dog with an orange collar standing in a dry cornfield">
    <defs>
      <linearGradient id="corn" x1="0" y1="0" x2="1" y2="1">
        <stop offset="0" stop-color="#e4ebcf" stop-opacity="0"/>
        <stop offset="0.3" stop-color="#c8ab6a"/>
        <stop offset="0.6" stop-color="#5c5a4c"/>
        <stop offset="1" stop-color="#6f6a33"/>
      </linearGradient>
    </defs>
    <rect width="297" height="188" fill="url(#corn)"/>
  </svg>

  <footer class="footer">
    <svg width="20" height="26" viewBox="0 0 20 26"><path d="M10 1C5 1 1.5 4.8 1.5 9.5 1.5 16 10 25 10 25s8.5-9 8.5-15.5C18.5 4.8 15 1 10 1z" fill="#c7a222"/><circle cx="10" cy="9.5" r="3.5" fill="#4c6125"/></svg>
    1470 Cedar Fork Road, Ashford, MO&nbsp; | &nbsp;zip code-65099
  </footer>
</main>
</body>
</html>
```